Brightlane Rapid Rinse Web Design

We are looking for a web design that highlights our state of the art fully automated commercial vehicle washing equipment. Similar system to a car wash however this system is meant for the largest vehicles on our roadways. Transport trucks with or without a trailer, busses both highway and school, RV's from 5th wheel type to A Class. Cement trucks, dump trucks, vac trucks, fuel trucks etc. Pick ups with utility trailers...Refrigerator truck clean outs.
Brightlane Rapid Rinse will wash your vehicle quickly and with a minimal impact on the environment

Home page
About us
Why Brightlane
Services and pricing
Videos of wash system
Fleets
contact us

Target Market(s)

Commercial vehicle owners and operators as well as corporate fleets. Includes busses, municipal, school and highway.both school and

Industry/Entity Type

transportation

Coding

Coded - Design and coding required

Number of Pages Required

5+ page

Font styles to use
Sans Serif

Colors
0054AA
0677BA
7BADD7
CADEEF
E8F1F8

Requirements
Must have
• Welcome page,why us page which describes the financial and environmental benefits. payment processing page, contact us page, Services which is washing vehicles and greasing for commercial vehicles that want that service and grease
Nice to have
• pictures of both clean and dirty commercial vehicles ie. before and after

```html
<!DOCTYPE html>
<html lang="en">
<head>
<meta charset="utf-8">
<title>Brightlane Rapid Rinse</title>
<link rel="stylesheet" href="https://fonts.googleapis.com/css2?family=Fira+Sans:wght@300;400;500;600;700&family=Lato:wght@400;700&display=swap">
<style>
:root{
  --navy:#0054AA;
  --blue:#0677BA;
  --sky:#7BADD7;
  --mist:#CADEEF;
  --ice:#E8F1F8;
  --ink:#222a33;
  --text:#444b52;
  --footer:#0b0c0e;
  --white:#ffffff;
}
*{margin:0;padding:0;box-sizing:border-box}
html,body{width:1200px;height:4121px;overflow:hidden}
body{position:relative;background:var(--white);font-family:"Lato",sans-serif;color:var(--text)}
.abs{position:absolute}
h1,h2,h3,h4,.brand{font-family:"Fira Sans",sans-serif}

/* header */
.site-header{position:absolute;left:0;top:0;width:1200px;height:85px;background:var(--blue);z-index:3}
.brand{position:absolute;color:var(--white);font-weight:600;line-height:1}
.brand .name{font-size:30px;display:flex;align-items:center;gap:8px}
.brand .dot{width:12px;height:12px;border-radius:50%;background:var(--sky);display:inline-block}
.brand .tag{font-size:15px;font-weight:400;letter-spacing:7.4px;margin-top:6px;padding-left:6px}
.site-header .brand{left:112px;top:16px}
.main-nav{position:absolute;top:31px;left:0;font-family:"Fira Sans",sans-serif;font-size:16px;color:var(--white)}
.main-nav span{position:absolute;white-space:nowrap}

/* hero */
.hero{position:absolute;left:0;top:85px;width:1200px;height:600px;
  background:linear-gradient(90deg,rgba(20,70,130,.85) 0%,rgba(40,80,120,.55) 40%,rgba(0,0,0,0) 70%),
  linear-gradient(160deg,#5c6a5a 0%,#7a7a6a 35%,#8e8470 60%,#b9ac8c 100%)}
.hero-title{position:absolute;left:106px;top:140px;color:var(--white);line-height:1.06}
.hero-title .l1{font-size:74px;font-weight:700;display:block}
.hero-title .l2{font-size:72px;font-weight:300;display:block}
.btn{position:absolute;height:44px;border-radius:22px;font-family:"Fira Sans",sans-serif;font-weight:600;font-size:14px;color:var(--white);display:flex;align-items:center;justify-content:center}
.btn-solid{background:var(--blue)}
.btn-ghost{border:2px solid var(--white)}
.hero-tag{position:absolute;left:0;top:558px;height:42px;width:264px;background:var(--blue);clip-path:polygon(0 0,248px 0,264px 42px,0 42px);color:var(--white);font-family:"Fira Sans",sans-serif;font-size:18px;padding:11px 0 0 16px;letter-spacing:.3px}

/* section titles */
.section-title{position:absolute;left:0;width:1200px;text-align:center;font-weight:600;font-size:35px;color:var(--ink);line-height:1.4}
.rule{position:absolute;left:559px;width:82px;height:4px;background:var(--blue)}

/* welcome */
.welcome{position:absolute;left:0;top:685px;width:1200px;height:649px;
  background:linear-gradient(100deg,#fff 0%,#fff 45%,#eef1f4 75%,#e3e8ee 100%)}
.photo{position:absolute}
.mission h3{position:absolute;left:640px;top:253px;font-size:30px;font-weight:500;color:var(--ink)}
.mission p{position:absolute;left:642px;top:318px;width:432px;font-size:16px;line-height:25.6px;color:var(--text)}

/* services */
.card{position:absolute;top:1506px;width:308px;height:403px;background:var(--white);box-shadow:0 2px 12px rgba(0,0,0,.08);border-bottom:4px solid var(--blue)}
.card .photo{left:0;top:0;width:308px;height:178px}
.card h4{position:absolute;left:26px;top:215px;font-size:20px;font-weight:500;color:var(--ink)}
.card p{position:absolute;left:26px;top:262px;width:250px;font-size:14.5px;line-height:25px;color:var(--text)}
.card svg{position:absolute;right:0;bottom:0}

/* video */
.video-band{position:absolute;left:0;top:2013px;width:1200px;height:472px;background:linear-gradient(90deg,#123d70 0%,#1b4a7c 50%,#123a6a 100%)}
.video-frame{position:absolute;left:197px;top:2179px;width:806px;height:397px;border:3px solid var(--blue);border-radius:10px;overflow:hidden;box-shadow:0 12px 24px rgba(0,0,0,.25)}

/* pricing */
.price-card{position:absolute;top:2781px;width:336px;height:278px;background:var(--white);border:1px dashed #cfd4d9;box-shadow:6px 6px 0 -1px #f1f2f4,6px 6px 0 0 #dfe2e6}
.price-card h4{position:absolute;left:26px;top:30px;font-size:20px;font-weight:500;color:var(--ink)}
.price-card .price{position:absolute;left:26px;top:72px;font-family:"Fira Sans",sans-serif;font-size:40px;font-weight:500;color:var(--ink)}
.price-card .price sup{font-size:15px;vertical-align:top;position:relative;top:6px;margin-right:4px}
.price-card p{position:absolute;left:26px;top:142px;width:282px;font-size:14px;line-height:21.5px;color:var(--text)}
.link{position:absolute;left:26px;font-family:"Fira Sans",sans-serif;font-size:14px;font-weight:600;color:var(--blue);display:flex;align-items:center;gap:8px}

/* before and after */
.gallery{position:absolute;left:0;top:3155px;width:1200px;height:573px;background:linear-gradient(90deg,#eef0f2 0%,#f7f7f8 45%,#e6e9ec 100%)}
.ba-label{position:absolute;font-family:"Fira Sans",sans-serif;font-size:25px;font-weight:500;color:#333;width:210px;text-align:center}

/* footer */
.site-footer{position:absolute;left:0;top:3728px;width:1200px;height:393px;background:var(--footer);color:var(--white)}
.site-footer .brand{left:112px;top:128px}
.col-title{position:absolute;font-family:"Fira Sans",sans-serif;font-size:18px;font-weight:600;color:var(--white)}
.f-item{position:absolute;display:flex;align-items:center;gap:10px;font-size:12.5px;line-height:16px}
.f-icon{width:24px;height:24px;border-radius:50%;background:var(--blue);flex:none;display:flex;align-items:center;justify-content:center}
.f-menu{position:absolute;left:749px;top:112px;font-size:12.5px;line-height:20.8px}
.f-rule{position:absolute;left:117px;top:312px;width:966px;height:1px;background:#9aa0a6}
.copyright{position:absolute;left:0;width:1200px;top:353px;text-align:center;font-size:12px}
</style>
</head>
<body>

<header class="site-header">
  <div class="brand"><div class="name">Brightlane <span class="dot"></span></div><div class="tag">Rapid Rinse</div></div>
  <nav class="main-nav">
    <span style="left:514px">Home</span>
    <span style="left:590px">About us</span>
    <span style="left:686px">Why Brightlane</span>
    <span style="left:858px">Services and pricing</span>
    <span style="left:1032px">More &#9662;</span>
  </nav>
</header>

<section class="hero" role="img" aria-label="Large yellow dump truck being pressure washed on a dirt site">
  <h1 class="hero-title"><span class="l1">Brightlane</span><span class="l2">Rapid Rinse</span></h1>
  <span class="btn btn-solid" style="left:112px;top:322px;width:131px">Book a Wash</span>
  <span class="btn btn-ghost" style="left:253px;top:322px;width:120px">Learn More</span>
  <span class="btn btn-ghost" style="left:390px;top:322px;width:120px">Contact Us</span>
  <div class="hero-tag">LESS THAN 15 MINUTES</div>
</section>

<section class="welcome">
  <h2 class="section-title" style="top:68px">Welcome to<br>Brightlane Rapid Rinse</h2>
  <div class="rule" style="top:172px"></div>
  <div class="photo" role="img" aria-label="Worker washing a tanker truck inside a wash bay" style="left:112px;top:238px;width:472px;height:330px;background:linear-gradient(135deg,#6b5540 0%,#a88a66 40%,#d9c3a0 65%,#8a6e50 100%)"></div>
  <div class="mission">
    <h3>Mission Statement</h3>
    <p>Lorem ipsum dolor sit amet, consectetur adipiscing elit, sed do eiusmod tempor incididunt ut labore et dolore magna aliqua. Ut enim ad minim veniam, quis nostrud exercitation ullamco laboris nisi ut aliquip ex ea commodo consequat. Duis aute irure dolor in reprehenderit in voluptate velit esse cillum dolore eu fugiat nulla pariatur.</p>
  </div>
  <span class="btn btn-solid" style="left:642px;top:498px;width:120px">Learn More</span>
</section>

<h2 class="section-title" style="top:1408px">Our Services</h2>
<div class="rule" style="top:1466px"></div>

<article class="card" style="left:112px">
  <div class="photo" role="img" aria-label="Truck inside an automated wash tunnel with red brushes" style="background:linear-gradient(90deg,#8c9298 0%,#b8bec4 30%,#c23a3a 45%,#e8eaec 55%,#b8bec4 75%,#7d848a 100%)"></div>
  <h4>Automated Truck Wash</h4>
  <p>Lorem ipsum dolor sit amet, con-sectetur adipiscing elit, sed do eius-mod tempor incididunt ut labore et dolore magna aliqua.</p>
  <svg width="44" height="54" viewBox="0 0 44 54"><path d="M44 0 L44 54 L0 54 Z" fill="#0677BA"/><path d="M19 41 H33 M28 36 L33 41 L28 46" stroke="#fff" stroke-width="2" fill="none" stroke-linecap="round" stroke-linejoin="round"/></svg>
</article>
<article class="card" style="left:446px">
  <div class="photo" role="img" aria-label="Close view of truck wheels being sprayed with water" style="background:linear-gradient(135deg,#3a4048 0%,#7c848c 40%,#c9cdd2 70%,#5a6068 100%)"></div>
  <h4>Additional Services</h4>
  <p>Lorem ipsum dolor sit amet, con-sectetur adipiscing elit, sed do eius-mod tempor incididunt ut labore et dolore magna aliqua.</p>
  <svg width="44" height="54" viewBox="0 0 44 54"><path d="M44 0 L44 54 L0 54 Z" fill="#0677BA"/><path d="M19 41 H33 M28 36 L33 41 L28 46" stroke="#fff" stroke-width="2" fill="none" stroke-linecap="round" stroke-linejoin="round"/></svg>
</article>
<article class="card" style="left:780px">
  <div class="photo" role="img" aria-label="Row of fleet trucks parked at sunset" style="background:linear-gradient(180deg,#3c2a24 0%,#b0562a 35%,#6a3a28 55%,#1e1e22 100%)"></div>
  <h4>Fleet Services</h4>
  <p>Lorem ipsum dolor sit amet, con-sectetur adipiscing elit, sed do eius-mod tempor incididunt ut labore et dolore magna aliqua.</p>
  <svg width="44" height="54" viewBox="0 0 44 54"><path d="M44 0 L44 54 L0 54 Z" fill="#0677BA"/><path d="M19 41 H33 M28 36 L33 41 L28 46" stroke="#fff" stroke-width="2" fill="none" stroke-linecap="round" stroke-linejoin="round"/></svg>
</article>

<section class="video-band" role="img" aria-label="Tanker truck in a wash bay, tinted blue"></section>
<h2 class="section-title" style="top:2066px;color:var(--white)">Live Video Feed</h2>
<div class="rule" style="top:2123px"></div>
<div class="video-frame">
  <div role="img" aria-label="Worker spraying the wheels of a white tanker truck" style="position:absolute;inset:0;background:linear-gradient(90deg,#2a2e36 0%,#3c4048 22%,#a8acae 40%,#d6d8da 65%,#eceeef 100%)"></div>
  <svg class="abs" style="left:371px;top:166px" width="64" height="64" viewBox="0 0 64 64" aria-label="Play video"><circle cx="32" cy="32" r="31" fill="#0054AA" fill-opacity=".85"/><path d="M26 20 L45 32 L26 44 Z" fill="#fff"/></svg>
</div>

<h2 class="section-title" style="top:2668px">Pricing and Packages</h2>
<div class="rule" style="top:2726px"></div>

<article class="price-card" style="left:237px">
  <h4>Individual Pricing</h4>
  <div class="price"><sup>$</sup>49</div>
  <p>Present pricing for single washes and addi-tional services using tables or cards with dark blue borders and headings.</p>
  <span class="link" style="top:222px">See Pricing <svg width="16" height="10" viewBox="0 0 16 10"><path d="M1 5 H14 M10 1 L14 5 L10 9" stroke="#0677BA" stroke-width="1.6" fill="none" stroke-linecap="round"/></svg></span>
</article>
<article class="price-card" style="left:626px">
  <h4>Fleet Packages</h4>
  <div class="price"><sup>$</sup>60</div>
  <p>A place to outline fleet rates and benefits for companies. A link to Contact Us about the various fleet packages and customer loyalty cards</p>
  <span class="link" style="top:238px">See Packages <svg width="16" height="10" viewBox="0 0 16 10"><path d="M1 5 H14 M10 1 L14 5 L10 9" stroke="#0677BA" stroke-width="1.6" fill="none" stroke-linecap="round"/></svg></span>
</article>

<section class="gallery">
  <h2 class="section-title" style="top:50px">Before and After</h2>
  <div class="rule" style="top:107px"></div>
  <div class="photo" role="img" aria-label="Dirty cement mixer truck before washing" style="left:112px;top:141px;width:209px;height:204px;background:linear-gradient(180deg,#d07a3a 0%,#8a7a6a 45%,#5a4a3c 100%)"></div>
  <div class="photo" role="img" aria-label="Clean cement mixer truck after washing" style="left:338px;top:227px;width:209px;height:205px;background:linear-gradient(180deg,#7fb4e0 0%,#dfe6ec 45%,#8a9498 100%)"></div>
  <div class="ba-label" style="left:337px;top:187px">After</div>
  <div class="ba-label" style="left:111px;top:363px">Before</div>
  <div class="photo" role="img" aria-label="Muddy yellow dump truck before washing" style="left:651px;top:141px;width:209px;height:204px;background:linear-gradient(180deg,#c88a4a 0%,#a07040 45%,#4a3a2c 100%)"></div>
  <div class="photo" role="img" aria-label="Clean yellow dump truck after washing" style="left:877px;top:227px;width:209px;height:205px;background:linear-gradient(180deg,#2c3440 0%,#5a5440 40%,#d0a428 60%,#3a3a36 100%)"></div>
  <div class="ba-label" style="left:876px;top:187px">After</div>
  <div class="ba-label" style="left:650px;top:363px">Before</div>
  <span class="btn btn-solid" style="left:540px;top:471px;width:120px">View More</span>
</section>

<footer class="site-footer">
  <div class="brand"><div class="name">Brightlane <span class="dot"></span></div><div class="tag">Rapid Rinse</div></div>

  <h4 class="col-title" style="left:414px;top:55px">CONTACT US</h4>
  <div class="f-item" style="left:414px;top:127px"><span class="f-icon"><svg width="10" height="12" viewBox="0 0 10 12"><path d="M5 11 C2 7 1 5.5 1 4 A4 4 0 0 1 9 4 C9 5.5 8 7 5 11Z" fill="#fff"/><circle cx="5" cy="4" r="1.4" fill="#0677BA"/></svg></span><span>Lorem ipsum dolor sit amet,<br>consectetur adipiscing</span></div>
  <div class="f-item" style="left:414px;top:180px"><span class="f-icon"><svg width="11" height="11" viewBox="0 0 11 11"><path d="M2 1 L4 1 L5 3.5 L3.8 4.5 A6 6 0 0 0 6.5 7.2 L7.5 6 L10 7 L10 9 A1 1 0 0 1 9 10 A8 8 0 0 1 1 2 A1 1 0 0 1 2 1Z" fill="#fff"/></svg></span><span>Call Us<br>+1 555 010 2040</span></div>
  <div class="f-item" style="left:414px;top:233px"><span class="f-icon"><svg width="12" height="9" viewBox="0 0 12 9"><rect x="0.5" y="0.5" width="11" height="8" rx="1" fill="#fff"/><path d="M1 1 L6 5 L11 1" stroke="#0677BA" fill="none"/></svg></span><span>E mail Us<br>info@brightlanerapidrinse.com</span></div>

  <h4 class="col-title" style="left:747px;top:55px">MENU</h4>
  <div class="f-menu">Home<br>About us<br>Why Brightlane<br>Services and pricing<br>Videos of wash system<br>Fleets<br>contact us</div>

  <h4 class="col-title" style="left:970px;top:55px">FOLLOW US</h4>
  <div class="f-item" style="left:970px;top:121px"><span class="f-icon"></span><span>Like us on<br>FRIENDSHEET</span></div>
  <div class="f-item" style="left:970px;top:176px"><span class="f-icon"></span><span>Follow us on<br>SNAPGRID</span></div>
  <div class="f-item" style="left:970px;top:231px"><span class="f-icon"></span><span>Follow us on<br>Vidstream</span></div>

  <div class="f-rule"></div>
  <p class="copyright">Privacy Policy &nbsp;|&nbsp; Terms and Conditions &nbsp;|&nbsp; Copyright © 2023 All Rights Reserved</p>
</footer>

</body>
</html>
```